brightquokka.net we need a webpage designed for our new product

We need a webpage designed for our new range of products from our new brand. We have had a logo designed on sketchharbor (see attached) and we want to keep to this theme. Our first product is a range of affordable app controlled LED lightbulbs.

I have added some photos that we think is good inspirational material and would be good as a background to this website, but we want the site to look modern but not conventional. We would like something that makes our company look quirky not corporate.

Thats it

Target Market(s)

Our product is being stocked by big name online retailers in the UK, the page will get link through hits from our app. Our target market is gadget freaks of all ages.

Industry/Entity Type

It Company

Requirements
Must have
• We are going to need a help page, text to be uploaded next few days.

We need a contact page.

design my work on iOS and Android as most people will access page through their handset or tablet.
Should not have
• We do not want anything too corporate.

```html
<!DOCTYPE html>
<html lang="en">
<head>
<meta charset="utf-8">
<title>The bright quokka</title>
<link rel="stylesheet" href="https://fonts.googleapis.com/css2?family=Carlito:wght@400;700&family=Tinos&display=swap">
<style>
  :root {
    --bg-deep: #2a1a0c;
    --bg-warm: #6b4a12;
    --bg-gold: #8a6a10;
    --title-olive: #3f5416;
    --phone-gold: #f2c12e;
    --nav-dark: #141414;
    --nav-rim: #8a1f14;
    --white: #ffffff;
    --black: #000000;
    --green: #5cbf5c;
    --orange: #ee6a4f;
    --yellow: #f2c200;
    --blue: #5f86ef;
    --footer-text: #9a9a9a;
    --social: #5aa83a;
  }
  * { box-sizing: border-box; margin: 0; padding: 0; }
  html, body { width: 1024px; height: 1200px; overflow: hidden; }
  body {
    position: relative;
    font-family: "Carlito", "Calibri", sans-serif;
    background: var(--black);
  }
  .backdrop {
    position: absolute; left: 0; top: 0; width: 1024px; height: 1067px;
    background:
      radial-gradient(ellipse at 15% 10%, rgba(150,70,20,0.7), transparent 45%),
      radial-gradient(ellipse at 85% 10%, rgba(20,60,80,0.6), transparent 45%),
      radial-gradient(ellipse at 50% 70%, rgba(140,100,20,0.55), transparent 60%),
      linear-gradient(180deg, var(--bg-gold) 0%, var(--bg-warm) 40%, var(--bg-deep) 100%);
  }
  .logo {
    position: absolute; left: 118px; top: 18px; width: 106px; height: 123px;
    background: var(--white);
    display: flex; align-items: flex-end; justify-content: center; padding-bottom: 6px;
  }
  .logo span { font-size: 7.5px; font-weight: 700; color: #2f9a3a; letter-spacing: 0.2px; }
  .site-title {
    position: absolute; left: 236px; top: 14px;
    font-family: "Tinos", "Times New Roman", serif;
    font-size: 52px; color: var(--title-olive); opacity: 0.85; letter-spacing: -1px;
  }
  .phone {
    position: absolute; left: 728px; top: 27px; display: flex; align-items: center; gap: 10px;
    color: var(--phone-gold); font-size: 21px;
  }
  .nav {
    position: absolute; left: 433px; top: 82px; width: 475px; height: 37px;
    border-radius: 19px; background: var(--nav-dark);
    border: 2px solid var(--nav-rim); box-shadow: 0 0 0 3px rgba(0,0,0,0.35);
    display: flex; align-items: center; justify-content: space-around; padding: 0 10px;
  }
  .nav a { color: var(--white); text-decoration: none; font-size: 12.5px; }
  .slider {
    position: absolute; left: 112px; top: 160px; width: 800px; height: 442px;
    background: var(--black); border: 2px solid var(--black);
  }
  .slide-photo {
    position: absolute; left: 0; top: 0; width: 796px; height: 414px;
    background:
      radial-gradient(ellipse at 28% 60%, #e8dcd0 0%, #c9b29a 22%, transparent 40%),
      linear-gradient(180deg, #6a4a36 0%, #3a2418 55%, #5a3018 75%, #2a1608 100%);
  }
  .caption {
    position: absolute; left: 307px; top: 60px; width: 485px; height: 74px;
    background: rgba(80,70,70,0.6); color: var(--white);
    text-align: center; font-size: 19.5px; line-height: 29px; padding-top: 8px;
  }
  .slide-arrow {
    position: absolute; top: 422px; width: 14px; height: 14px; background: #444;
    display: flex; align-items: center; justify-content: center;
  }
  .slide-arrow.prev { left: 4px; }
  .slide-arrow.next { right: 4px; }
  .card { position: absolute; width: 332px; height: 139px; display: flex; }
  .card .stripe { width: 5px; }
  .card .thumb { width: 144px; }
  .card .body { flex: 1; padding: 8px 6px 0 7px; }
  .card h2 { font-weight: 400; font-size: 15.5px; color: #111; margin-bottom: 9px; }
  .card p { font-size: 10px; line-height: 14.4px; color: #1a1a1a; padding-left: 3px; }
  .card.green .stripe, .card.green .body { background: var(--green); }
  .card.orange .stripe, .card.orange .body { background: var(--orange); }
  .card.yellow .stripe, .card.yellow .body { background: var(--yellow); }
  .card.blue .stripe, .card.blue .body { background: var(--blue); }
  .footer {
    position: absolute; left: 0; top: 1067px; width: 1024px; height: 133px; background: var(--black);
  }
  .footer .legal {
    position: absolute; top: 46px; width: 100%; text-align: center;
    font-size: 10px; color: var(--footer-text);
  }
  .footer .social { position: absolute; top: 74px; left: 470px; display: flex; gap: 10px; }
  .footer .social span {
    width: 38px; height: 38px; border-radius: 50%;
    background: radial-gradient(circle at 40% 30%, #9ad86a, var(--social) 60%, #2f6a1e);
    border: 2px solid #d8d8d8; display: block;
  }
</style>
</head>
<body>
  <div class="backdrop" role="img" aria-label="Blurred photo of cheerful cartoon cat figurines on a shelf"></div>

  <header>
    <div class="logo"><span>BRIGHTQUOKKA</span></div>
    <div class="site-title">The bright quokka</div>
    <div class="phone">
      <svg width="26" height="26" viewBox="0 0 24 24" aria-hidden="true"><path fill="#f2c12e" d="M6.6 10.8a15.1 15.1 0 0 0 6.6 6.6l2.2-2.2c.3-.3.7-.4 1-.2 1.1.4 2.3.6 3.6.6.6 0 1 .4 1 1V20c0 .6-.4 1-1 1A17 17 0 0 1 3 4c0-.6.4-1 1-1h3.5c.6 0 1 .4 1 1 0 1.3.2 2.5.6 3.6.1.3 0 .7-.2 1z"/></svg>
      <span>1-800-555-0142</span>
    </div>
    <nav class="nav">
      <a href="#">FOR CONSUMERS</a>
      <a href="#">FOR PROFESSIONALS</a>
      <a href="#">ABOUT BRIGHT QUOKKA</a>
    </nav>
  </header>

  <section class="slider">
    <div class="slide-photo" role="img" aria-label="White ceramic seal lamp on a wooden table in a shop"></div>
    <div class="caption">OUR FIRST PRODUCT IS A RANGE OF<br>AFFORDABLE APP CONTROLLED LED LIGHTBULBS</div>
    <div class="slide-arrow prev"><svg width="8" height="6" viewBox="0 0 8 6"><path d="M8 3H1M3 1L1 3l2 2" stroke="#fff" fill="none"/></svg></div>
    <div class="slide-arrow next"><svg width="8" height="6" viewBox="0 0 8 6"><path d="M0 3h7M5 1l2 2-2 2" stroke="#fff" fill="none"/></svg></div>
  </section>

  <article class="card green" style="left:145px;top:646px">
    <div class="stripe"></div>
    <div class="thumb" role="img" aria-label="Hand holding a phone with a lighting app in a living room" style="background:linear-gradient(135deg,#6a4a2a,#2a2a2a 60%,#c8a080)"></div>
    <div class="body"><h2>SMART LED LIGHT APP</h2><p>Lorem Ipsum. Proin gravida nibh vel velit auctor aliquet. Aenean sollicitudin, lorem quis bibendum auctor, nisi elit consequat ipsum, nec sagittis sem nibh id elit. Duis</p></div>
  </article>

  <article class="card orange" style="left:534px;top:646px">
    <div class="stripe"></div>
    <div class="thumb" role="img" aria-label="Hands holding a tablet showing colourful pencils" style="background:linear-gradient(135deg,#8a94a8,#2a2a30 55%,#b0a090)"></div>
    <div class="body"><h2>LOREM IPSUM PROIN</h2><p>Lorem Ipsum. Proin gravida nibh vel velit auctor aliquet. Aenean sollicitudin, lorem quis bibendum auctor, nisi elit consequat ipsum, nec sagittis sem nibh id elit. Duis</p></div>
  </article>

  <article class="card yellow" style="left:145px;top:842px">
    <div class="stripe"></div>
    <div class="thumb" role="img" aria-label="Two smart LED bulbs glowing white and pink" style="background:linear-gradient(135deg,#5a2a5a,#2a1a2a 55%,#c05080)"></div>
    <div class="body"><h2>GRAVIDA NIBH &nbsp;VELIT</h2><p>Lorem Ipsum. Proin gravida nibh vel velit auctor aliquet. Aenean sollicitudin, lorem quis bibendum auctor, nisi elit consequat ipsum, nec sagittis sem nibh id elit. Duis</p></div>
  </article>

  <article class="card blue" style="left:534px;top:843px">
    <div class="stripe"></div>
    <div class="thumb" role="img" aria-label="Phone with a colour wheel app beside a smart bulb" style="background:linear-gradient(135deg,#3a3a8a,#1a1a3a 55%,#d8d8e0)"></div>
    <div class="body"><h2>VERSION &nbsp;OF LOREM</h2><p>Lorem Ipsum. Proin gravida nibh vel velit auctor aliquet. Aenean sollicitudin, lorem quis bibendum auctor, nisi elit consequat ipsum, nec sagittis sem nibh id elit. Duis</p></div>
  </article>

  <footer class="footer">
    <div class="legal">© 2014 &nbsp;brightquokka.net &nbsp;| &nbsp;PRIVACY POLICY</div>
    <div class="social">
      <span aria-label="Social link"></span>
      <span aria-label="Social link"></span>
    </div>
  </footer>
</body>
</html>
```